New website for concierge mobile medical service

new website for business:
WEBSITE REQUEST LIST:
Luxury product look.
Professional. Clean & simple, NO stock people photos. Graphics OK.
Black and white text.

```html
<!DOCTYPE html>
<html lang="en">
<head>
<meta charset="utf-8">
<title>FAQ – Lumen Care</title>
<link href="https://fonts.googleapis.com/css2?family=Lato:wght@400;700;900&display=swap" rel="stylesheet">
<style>
  :root {
    --ink: #222;
    --accent: #3d4ea3;
    --phone: #5b51a8;
    --navy: #0a3552;
    --hero-dark: #02080d;
    --border: #d2d2d2;
    --band-a: #1a8aa6;
    --band-b: #146d93;
    --button: #8ad0d8;
    --footer: #1f1f1f;
    --white: #fff;
  }
  * { box-sizing: border-box; margin: 0; padding: 0; }
  html, body { width: 917px; height: 1200px; overflow: hidden; }
  body { position: relative; font-family: 'Lato', sans-serif; color: var(--ink); background: var(--white); }

  .site-header { position: absolute; inset: 0 0 auto 0; height: 82px; background: var(--white); }
  .brand { position: absolute; left: 120px; top: 15px; width: 92px; height: 92px; border-radius: 50%;
    background: var(--navy); border: 5px solid var(--white); z-index: 3;
    display: flex; align-items: center; justify-content: center;
    color: var(--white); font-weight: 700; font-size: 14px; }
  .phone { position: absolute; left: 678px; top: 12px; display: flex; align-items: center; gap: 10px;
    color: var(--phone); font-weight: 700; font-size: 16px; }
  .phone-icon { width: 24px; height: 24px; background: var(--phone); border-radius: 2px;
    display: flex; align-items: center; justify-content: center; }
  .main-nav a { position: absolute; top: 58px; font-size: 9.5px; font-weight: 700; color: var(--ink); text-decoration: none; }
  .main-nav a.active { color: var(--accent); }
  .nav-marker { position: absolute; left: 681px; top: 78px; width: 51px; height: 4px; background: var(--navy); }

  .hero { position: absolute; left: 0; top: 82px; width: 917px; height: 202px;
    background: linear-gradient(90deg, var(--hero-dark) 0%, #062a40 55%, var(--navy) 100%); }
  .hero h1 { position: absolute; left: 109px; top: 80px; font-size: 34px; font-weight: 900; color: var(--white); }
  .hero-art { position: absolute; left: 661px; top: 23px; width: 156px; height: 156px; border-radius: 50%;
    border: 2px solid #6fd8e8; background: radial-gradient(circle, #0f4566 0%, #0a3552 70%); }

  .faq-list { position: absolute; left: 111px; top: 322px; width: 696px; }
  .faq-item { position: absolute; left: 0; width: 696px; border: 1px solid var(--border); border-radius: 2px;
    padding: 10px 40px 0 12px; }
  .faq-q { font-size: 15px; font-weight: 700; line-height: 22px; }
  .faq-item.open .faq-q { color: var(--accent); }
  .faq-a { margin-top: 9px; font-size: 10.5px; line-height: 17.7px; }
  .faq-toggle { position: absolute; right: 12px; top: 14px; width: 13px; height: 13px; }

  .subscribe { position: absolute; left: 0; top: 904px; width: 917px; height: 193px;
    background: linear-gradient(100deg, var(--band-a) 0%, var(--band-b) 50%, #1a86a8 100%); }
  .subscribe h2 { position: absolute; left: 0; right: 0; top: 34px; text-align: center;
    font-size: 25px; font-weight: 700; color: var(--white); }
  .field { position: absolute; top: 79px; width: 243px; height: 34px; background: var(--white);
    padding-left: 12px; font-size: 9.5px; line-height: 34px; color: #333; }
  .subscribe-btn { position: absolute; left: 211px; top: 119px; width: 495px; height: 34px; background: var(--button);
    color: var(--white); font-size: 11.5px; font-weight: 700; text-align: center; line-height: 34px; }

  .site-footer { position: absolute; left: 0; top: 1097px; width: 917px; height: 103px; background: var(--footer); color: var(--white); }
  .footer-nav a { position: absolute; top: 19px; font-size: 9.5px; font-weight: 700; color: var(--white); text-decoration: none; }
  .copyright { position: absolute; left: 0; right: 0; top: 44px; text-align: center; font-size: 8.6px; }
  .social { position: absolute; top: 68px; width: 12px; height: 12px; border-radius: 50%; background: var(--white); }
</style>
</head>
<body>
  <header class="site-header">
    <div class="brand">Lumen Care</div>
    <div class="phone">
      <span class="phone-icon">
        <svg width="12" height="12" viewBox="0 0 24 24"><path fill="#fff" d="M6.6 10.8a15 15 0 0 0 6.6 6.6l2.2-2.2a1 1 0 0 1 1-.25 11.4 11.4 0 0 0 3.6.57 1 1 0 0 1 1 1V20a1 1 0 0 1-1 1A17 17 0 0 1 3 4a1 1 0 0 1 1-1h3.5a1 1 0 0 1 1 1c0 1.25.2 2.45.57 3.57a1 1 0 0 1-.25 1z"/></svg>
      </span>
      555-014-0192
    </div>
    <nav class="main-nav">
      <a style="left:301px">HOME</a>
      <a style="left:362px">ABOUT US</a>
      <a style="left:442px">WHY LUMEN?</a>
      <a style="left:531px">SERVICE AREA</a>
      <a style="left:631px">OTHER</a>
      <a class="active" style="left:695px">FAQ</a>
      <a style="left:745px">CONTACT US</a>
    </nav>
    <div class="nav-marker"></div>
  </header>

  <section class="hero">
    <h1>FAQ</h1>
    <div class="hero-art" role="img" aria-label="Line illustration of a house-call car with a medical emblem"></div>
  </section>

  <main class="faq-list">
    <div class="faq-item" style="top:0;height:40px"><p class="faq-q">What limitations are there for treating me at my home?</p>
      <svg class="faq-toggle" viewBox="0 0 20 20"><circle cx="10" cy="10" r="10" fill="var(--accent)"/><path d="M8 5.5l4.5 4.5L8 14.5" stroke="#fff" stroke-width="2.6" fill="none"/></svg></div>
    <div class="faq-item open" style="top:49px;height:93px"><p class="faq-q">How do I know if I should go to the ER or call Lumen Care?</p>
      <p class="faq-a">You should always call 911 in the event of an emergency or if you need immediate treatment. If you are considering a trip to the urgent care or not quite sure if you need to go to the ER, please message us and we will call you and walk you through the decision.</p>
      <svg class="faq-toggle" viewBox="0 0 20 20"><circle cx="10" cy="10" r="10" fill="var(--accent)"/><path d="M5.5 8l4.5 4.5L14.5 8" stroke="#fff" stroke-width="2.6" fill="none"/></svg></div>
    <div class="faq-item" style="top:152px;height:40px"><p class="faq-q">Will the doctor always be the one to come to my home?</p>
      <svg class="faq-toggle" viewBox="0 0 20 20"><circle cx="10" cy="10" r="10" fill="var(--accent)"/><path d="M8 5.5l4.5 4.5L8 14.5" stroke="#fff" stroke-width="2.6" fill="none"/></svg></div>
    <div class="faq-item" style="top:204px;height:40px"><p class="faq-q">This seems very comprehensive. Should I cancel or change my health insurance?</p>
      <svg class="faq-toggle" viewBox="0 0 20 20"><circle cx="10" cy="10" r="10" fill="var(--accent)"/><path d="M8 5.5l4.5 4.5L8 14.5" stroke="#fff" stroke-width="2.6" fill="none"/></svg></div>
    <div class="faq-item" style="top:255px;height:63px"><p class="faq-q">I'm on Medicare, it seems like I might be able to modify one of my supplemental policies, can you advise me on this?</p>
      <svg class="faq-toggle" viewBox="0 0 20 20"><circle cx="10" cy="10" r="10" fill="var(--accent)"/><path d="M8 5.5l4.5 4.5L8 14.5" stroke="#fff" stroke-width="2.6" fill="none"/></svg></div>
    <div class="faq-item" style="top:328px;height:40px"><p class="faq-q">How do I know that my health information is secure?</p>
      <svg class="faq-toggle" viewBox="0 0 20 20"><circle cx="10" cy="10" r="10" fill="var(--accent)"/><path d="M8 5.5l4.5 4.5L8 14.5" stroke="#fff" stroke-width="2.6" fill="none"/></svg></div>
    <div class="faq-item" style="top:378px;height:40px"><p class="faq-q">Will I get any surprise bills from Lumen Care after I receive treatment?</p>
      <svg class="faq-toggle" viewBox="0 0 20 20"><circle cx="10" cy="10" r="10" fill="var(--accent)"/><path d="M8 5.5l4.5 4.5L8 14.5" stroke="#fff" stroke-width="2.6" fill="none"/></svg></div>
    <div class="faq-item" style="top:429px;height:40px"><p class="faq-q">What if I need to see a specialist?</p>
      <svg class="faq-toggle" viewBox="0 0 20 20"><circle cx="10" cy="10" r="10" fill="var(--accent)"/><path d="M8 5.5l4.5 4.5L8 14.5" stroke="#fff" stroke-width="2.6" fill="none"/></svg></div>
    <div class="faq-item" style="top:480px;height:40px"><p class="faq-q">I'm a veteran. Do I get a discount?</p>
      <svg class="faq-toggle" viewBox="0 0 20 20"><circle cx="10" cy="10" r="10" fill="var(--accent)"/><path d="M8 5.5l4.5 4.5L8 14.5" stroke="#fff" stroke-width="2.6" fill="none"/></svg></div>
  </main>

  <section class="subscribe" role="img" aria-label="Teal background with faint medical hexagon graphics">
    <h2>Subscribe</h2>
    <div class="field" style="left:211px">Enter Name</div>
    <div class="field" style="left:463px">Enter Email Address</div>
    <div class="subscribe-btn">SUBSCRIBE NOW</div>
  </section>

  <footer class="site-footer">
    <nav class="footer-nav">
      <a style="left:230px">HOME</a>
      <a style="left:292px">ABOUT US</a>
      <a style="left:372px">WHY LUMEN?</a>
      <a style="left:460px">SERVICE AREA</a>
      <a style="left:560px">OTHER</a>
      <a style="left:624px">CONTACT US</a>
    </nav>
    <p class="copyright">Copyright © 2019.&nbsp; Company Name&nbsp; All Rights Reserved</p>
    <span class="social" style="left:399px" aria-label="Social link"></span>
    <span class="social" style="left:424px" aria-label="Social link"></span>
    <span class="social" style="left:451px" aria-label="Social link"></span>
    <span class="social" style="left:477px" aria-label="Social link"></span>
    <span class="social" style="left:503px" aria-label="Social link"></span>
  </footer>
</body>
</html>
```